Animal Eye Clinic needs a Business card

We are a new veterinary ophthalmology practice (Ridgeline Pet Vision Care) and we need a business card designed. We only see animal eyes - we are not a regular veterinary clinic. We already have a logo. We are looking for a professional, good looking business card to hand out to our clients. We are looking for something simple but professional and contemporary. Our logo is likely the only picture/graphic that needs to be on the card.
Updates

Contact Information for Business Card

Delia Vossman, BSc, DVM, MSc, DipACVO
Veterinary Ophthalmologist

Phone: 250.418.3927
Email: ridgelinepetvisioncare@mailbox-example.net
Website: ridgelinepetvisioncare-example.net
Address: 1874 Thornbury Rd
Kelowna, BC, V1X 4M9

Colors

Designer to choose colors to be used in the design.

Requirements
Must have
• Our logo (attached)

```html
<!DOCTYPE html>
<html lang="en">
<head>
<meta charset="utf-8">
<title>Ridgeline Pet Vision Care – Business Card</title>
<link href="https://fonts.googleapis.com/css2?family=Open+Sans:wght@400;600;700&display=swap" rel="stylesheet">
<style>
  :root {
    --teal: #0596a8;
    --teal-deep: #067f8f;
    --slate: #7a7a7a;
    --white: #ffffff;
    --backdrop: #d9d9d9;
    --ink: #4a4a4a;
  }
  * { box-sizing: border-box; margin: 0; padding: 0; }
  html, body { width: 1200px; height: 802px; overflow: hidden; }
  body {
    background: var(--backdrop);
    font-family: "Open Sans", Arial, sans-serif;
    position: relative;
  }
  .card {
    position: absolute;
    top: 274px;
    width: 442px;
    height: 264px;
    box-shadow: 0 3px 6px rgba(0,0,0,0.35);
    overflow: hidden;
  }
  .card--front { left: 136px; background: var(--teal); color: var(--white); }
  .card--back { left: 624px; background: var(--white); }

  .animal-art {
    position: absolute;
    right: 0;
    top: 0;
    width: 182px;
    height: 264px;
    background: linear-gradient(160deg, var(--teal-deep) 0%, var(--teal) 45%, var(--slate) 100%);
  }
  .identity { position: absolute; left: 22px; top: 31px; }
  .identity__name { font-size: 14px; font-weight: 700; letter-spacing: 0.2px; }
  .identity__creds, .identity__role { font-size: 11px; line-height: 16px; }
  .identity__creds { margin-top: 2px; }

  .address { position: absolute; left: 22px; top: 145px; font-size: 11px; line-height: 16px; }
  .contact { position: absolute; left: 22px; top: 191px; list-style: none; font-size: 10.5px; line-height: 16px; }
  .contact li { display: flex; align-items: center; gap: 4px; }
  .contact svg { width: 9px; height: 9px; fill: var(--white); flex: none; }

  .brand {
    position: absolute;
    left: 0; right: 0; top: 50%;
    transform: translateY(-50%);
    display: flex;
    align-items: center;
    justify-content: center;
    gap: 10px;
  }
  .brand__dot { width: 22px; height: 22px; border-radius: 50%; background: var(--teal); }
  .brand__name { font-size: 22px; font-weight: 600; color: var(--teal); }
</style>
</head>
<body>
  <section class="card card--front">
    <div class="animal-art" role="img" aria-label="Silhouettes of a horse, a dog and a cat in teal, white and grey"></div>
    <div class="identity">
      <h1 class="identity__name">DELIA VOSSMAN</h1>
      <p class="identity__creds">BSC, DVM, MSC, DIPACVO</p>
      <p class="identity__role">Veterinary Ophthalmologist</p>
    </div>
    <address class="address" style="font-style:normal">
      1874 Thornbury Rd<br>
      Kelowna, BC, V1X 4M9
    </address>
    <ul class="contact">
      <li><svg viewBox="0 0 10 10"><path d="M2 1h2l1 2-1.2 1a5 5 0 0 0 2.2 2.2L7 5l2 1v2c0 .6-.4 1-1 1A8 8 0 0 1 1 2c0-.6.4-1 1-1z"/></svg>250.418.3927</li>
      <li><svg viewBox="0 0 10 10"><path d="M0 2h10v6H0z M0 2l5 3.5L10 2" stroke="#0596a8" stroke-width="0.8"/></svg>ridgelinepetvisioncare@mailbox-example.net</li>
      <li><svg viewBox="0 0 10 10"><circle cx="5" cy="5" r="4.5"/><path d="M0.5 5h9M5 0.5v9" stroke="#0596a8" stroke-width="0.7"/></svg>ridgelinepetvisioncare-example.net</li>
    </ul>
  </section>

  <section class="card card--back">
    <div class="brand">
      <span class="brand__dot"></span>
      <span class="brand__name">Ridgeline Pet Vision Care</span>
    </div>
  </section>
</body>
</html>
```